Brindle Healthcare Coming Soon Sign

I need a large (10 x5) road banner announcing the construction of our new medical practice at 5187 Larkmoor Road in John's Island. The name of our practice is Brindle Healthcare and we thought it would be fund to nick name it the "Brindle Waystation". We'd like the tagline to read - "There's nothing healthy about driving an hour to see your doctor. So we're coming to you." Opening Late 2025 I have attached three logos as we have two other practices (Brindle Urgent and Brindle Aesthetics ) that should be present on the bottom of the sign but the main business is Brindle Healthcare. For more information on our look/feel visit our website www.goplainway-example.com (which should be somewhere on the banner as well)
Updates

The signage needs to say Coming Late Fall 2025!

Target Market(s)

Drive By traffic must be made aware that we are coming soon

Industry/Entity Type

Healthcare

Requirements
Nice to have
• Western Theme

```html
<!DOCTYPE html>
<html lang="en">
<head>
<meta charset="utf-8">
<title>Brindle Healthcare – Coming Late Fall 2025 Road Banner</title>
<link rel="stylesheet" href="https://fonts.googleapis.com/css2?family=Oswald:wght@500;600&family=Rye&family=Smokum&display=swap">
<style>
  :root {
    --page-bg: #bdbdbd;
    --cream: #fbf9e6;
    --cloud: #eef0e4;
    --wood-dark: #5c2c15;
    --wood: #7e4325;
    --wood-light: #94552f;
    --ink: #171717;
    --teal-ink: #173c4c;
    --navy: #0b1f55;
    --brand-blue: #4f9fd6;
    --brand-pink: #e3137d;
    --brand-red: #ee4236;
    --white: #ffffff;
    --display-font: "Smokum", "Oswald", sans-serif;
    --text-font: "Rye", serif;
  }
  * { box-sizing: border-box; margin: 0; padding: 0; }
  html, body {
    width: 947px; height: 1200px; overflow: hidden;
    background: var(--page-bg);
  }
  .banner {
    position: absolute;
    left: 23px; top: 375px;
    width: 900px; height: 450px;
    overflow: hidden;
    background: var(--cream);
    box-shadow: 0 6px 14px rgba(0,0,0,.35);
  }
  .banner__sky {
    position: absolute; inset: 0 0 150px 0;
    background:
      radial-gradient(ellipse 120px 70px at 12% 55%, var(--cloud), transparent 70%),
      radial-gradient(ellipse 150px 80px at 45% 20%, var(--cloud), transparent 70%),
      radial-gradient(ellipse 140px 80px at 85% 45%, var(--cloud), transparent 70%),
      var(--cream);
  }
  .brand-main {
    position: absolute; top: 40px; left: 0; right: 0;
    display: flex; align-items: center; justify-content: center; gap: 12px;
  }
  .brand-main__square {
    width: 30px; height: 30px; background: var(--brand-blue); border-radius: 4px;
  }
  .brand-main__name {
    font-family: var(--text-font); font-size: 30px; color: var(--navy);
    letter-spacing: 2px; text-transform: uppercase;
  }
  .plank {
    position: absolute; left: 93px; top: 112px; width: 717px; height: 93px;
  }
  .plank svg { position: absolute; inset: 0; width: 100%; height: 100%; }
  .plank__text {
    position: absolute; inset: 0 40px;
    display: flex; align-items: center; justify-content: center;
    font-family: var(--display-font); font-weight: 600;
    font-size: 60px; line-height: 1;
    color: var(--white); white-space: nowrap; letter-spacing: 1px;
    overflow: hidden;
  }
  .tagline {
    position: absolute; left: 0; right: 0; top: 212px;
    text-align: center; font-family: var(--text-font); white-space: nowrap;
    text-transform: uppercase; line-height: 34px;
  }
  .tagline__lead { font-size: 24px; color: var(--teal-ink); }
  .tagline__rest { font-size: 23px; color: var(--ink); }
  .skyline {
    position: absolute; left: 0; right: 0; top: 299px; height: 46px;
    background: linear-gradient(to bottom, rgba(11,31,85,.55), var(--navy) 70%);
  }
  .footer-band {
    position: absolute; left: 0; right: 0; top: 343px; bottom: 0;
    background: var(--navy);
    display: flex; align-items: center; justify-content: space-between;
    padding: 0 34px;
  }
  .sub-brand {
    display: flex; align-items: center; gap: 8px;
    font-family: var(--text-font); font-size: 14px; letter-spacing: 1px;
    text-transform: uppercase; white-space: nowrap;
  }
  .sub-brand__mark { width: 26px; height: 26px; flex: none; }
  .sub-brand--aesthetics { color: var(--brand-pink); }
  .sub-brand--aesthetics .sub-brand__mark { background: var(--brand-pink); border-radius: 50%; }
  .sub-brand--urgent { color: var(--brand-red); }
  .sub-brand--urgent .sub-brand__mark { background: var(--brand-red); border-radius: 3px; }
  .web-address {
    font-family: var(--display-font); font-weight: 500;
    font-size: 30px; color: var(--white);
    letter-spacing: 1px; white-space: nowrap;
  }
</style>
</head>
<body>
  <main class="banner">
    <div class="banner__sky" role="img" aria-label="Soft cream sky with faint clouds and birds"></div>

    <div class="brand-main">
      <span class="brand-main__square"></span>
      <span class="brand-main__name">Brindle Healthcare</span>
    </div>

    <div class="plank">
      <svg viewBox="0 0 717 93" preserveAspectRatio="none" role="img" aria-label="Wooden sign plank">
        <defs>
          <linearGradient id="woodTone" x1="0" y1="0" x2="0" y2="1">
            <stop offset="0" stop-color="#94552f"/>
            <stop offset=".5" stop-color="#7e4325"/>
            <stop offset="1" stop-color="#5c2c15"/>
          </linearGradient>
        </defs>
        <path d="M22 4 H695 L705 14 Q717 46 705 79 L695 89 H22 L12 79 Q0 46 12 14 Z"
              fill="url(#woodTone)" stroke="#2a1a12" stroke-width="3"/>
        <path d="M28 10 H689 L698 19 Q708 46 698 74 L689 83 H28 L19 74 Q9 46 19 19 Z"
              fill="none" stroke="#f2e6d0" stroke-width="1.5" opacity=".7"/>
      </svg>
      <div class="plank__text">COMING LATE FALL 2025</div>
    </div>

    <p class="tagline">
      <span class="tagline__lead">Conserving Rural John's Island</span><br>
      <span class="tagline__rest">With Home Grown Progressive Primary Care</span>
    </p>

    <div class="skyline" role="img" aria-label="Navy city skyline silhouette with a cable bridge"></div>

    <footer class="footer-band">
      <div class="sub-brand sub-brand--aesthetics">
        <span class="sub-brand__mark"></span>
        <span>Brindle Aesthetics</span>
      </div>
      <div class="web-address">www.goplainway-example.com</div>
      <div class="sub-brand sub-brand--urgent">
        <span class="sub-brand__mark"></span>
        <span>Brindle Urgent</span>
      </div>
    </footer>
  </main>
</body>
</html>
```